Brightleaf Rx Pass reinvent our website.

Our Website is outdated and needs an overhaul, in every aspect. We assist individuals that have little or no prescription coverage and allow them to receive a discount ranging from 33% up to 78% for free. In the beginning we utilized pharmacies to spread the word, but times have a changed. We are looking for a modern and clean site. We are open to anything, image, logo etc.

Tallymart Market(s)

Anyone regardless of residency, age or income. This program is designed to assist those that have NO prescription coverage or for those whose particular prescription may not be covered by insurance.

Industry/Entity Type

Pharmaceutical

Coding

Coded - Design and coding required

Number of Pages Required

4 page

Requirements
Must have
• -The two MUST haves are the pharmacy locators & drug pricing. If you can combine the 2, even better.
• -a ongoing counter/tally on the 1stpage reflecting the amount of money we are saving customers. http://widgetmarto.net/item/motion-tickers-v-20-flux-pack-collection/full_screen_preview/52907314
• -on a smart phone the ability to view the information that is needed to get the actual discount for the medication.
Nice to have
• animated tutorial showing how to use the card
• health blog

```html
<!DOCTYPE html>
<html lang="en">
<head>
<meta charset="utf-8">
<title>Brightleaf Rx Pass</title>
<link href="https://fonts.googleapis.com/css2?family=Roboto:ital,wght@0,300;0,400;0,500;0,700;1,400&family=Open+Sans:wght@400;600&display=swap" rel="stylesheet">
<style>
:root{
  --blue:#1d5ba6;
  --blue-dark:#174a8a;
  --red:#ec3833;
  --text:#333;
  --muted:#666;
  --light:#f6f6f6;
  --footer-bar:#3a3a3a;
  --white:#fff;
}
*{margin:0;padding:0;box-sizing:border-box}
html,body{width:1200px;height:2242px;overflow:hidden}
body{position:relative;font-family:"Roboto",sans-serif;color:var(--text);background:var(--white)}
.abs{position:absolute}
.top-rule{left:0;top:0;width:1200px;height:3px;background:var(--blue)}
.social{left:99px;top:53px;display:flex;gap:5px}
.social span{width:30px;height:30px;border-radius:50%;border:1.5px solid var(--blue);display:block}
.social span:last-child{border-color:var(--red)}
.brand{left:500px;top:44px;display:flex;align-items:center;gap:10px;font-family:"Roboto",sans-serif;font-weight:700;font-size:28px;color:var(--blue)}
.brand i{width:26px;height:26px;border-radius:50%;background:var(--red);display:block}
.contact-top{left:884px;top:52px;display:flex;gap:14px;font-family:"Open Sans",sans-serif;font-size:15px;color:#444;line-height:1.25}
.contact-top .ico{width:34px;height:34px;border-radius:50%;background:var(--blue);display:flex;align-items:center;justify-content:center;margin-top:2px}
.hero{left:0;top:161px;width:1200px;height:511px;background:linear-gradient(100deg,#e9e2d8 0%,#cdb8a0 30%,#8c7a69 55%,#5e5650 72%,#b8b6b3 100%)}
.nav{left:99px;top:138px;width:1002px;height:53px;border-radius:27px;background:linear-gradient(var(--blue),var(--blue-dark));display:flex;overflow:hidden;z-index:2}
.nav a{color:var(--white);text-decoration:none;font-size:13.5px;display:flex;align-items:center;justify-content:center;padding:0 26px;border-right:1px solid rgba(255,255,255,.18);text-transform:uppercase}
.nav a.active{background:var(--red);padding:0 36px}
.hero-arrow{top:388px}
.hero-copy{left:727px;top:355px;color:var(--white);width:400px}
.hero-copy h1{font-family:"Roboto",sans-serif;font-weight:700;font-size:40px;line-height:1;text-shadow:0 2px 4px rgba(0,0,0,.35);letter-spacing:.3px;margin-bottom:12px}
.hero-copy p{font-size:18px;line-height:1.4;margin-left:3px}
.btn{display:inline-block;background:var(--red);color:var(--white);border-radius:24px;font-size:16px;text-transform:uppercase;text-align:center}
.hero-copy .btn{margin-top:18px;margin-left:1px;padding:11px 26px;border:2px solid var(--white)}
.mission{left:0;top:672px;width:1200px;height:192px}
.mission-title{left:142px;top:731px;color:var(--white);font-size:31px;line-height:1.3;font-weight:500}
.mission-text{left:376px;top:704px;width:690px;color:var(--white);font-size:12.5px;line-height:1.65}
.mission-text p+p{margin-top:8px}
.howto{left:0;top:864px;width:1200px;height:808px;background:linear-gradient(160deg,#fff 0%,#f4f4f5 45%,#fff 100%)}
.howto-head{left:0;top:906px;width:1200px;text-align:center}
.howto-head h2{font-weight:400;font-size:32px;color:#333}
.howto-head h2 em{font-style:normal;color:var(--red)}
.howto-head a{font-size:15px;color:var(--blue);text-decoration:none}
.step{top:1004px;width:300px;text-align:center}
.step .circle{width:96px;height:96px;border-radius:50%;background:var(--blue);margin:0 auto 20px;display:flex;align-items:center;justify-content:center;color:var(--white);font-size:50px;font-weight:500}
.step h3{font-weight:400;font-size:19px;color:#444;margin-bottom:10px}
.step p{font-size:12px;line-height:1.7;color:#555;padding:0 12px}
.program-photo{left:114px;top:1270px;width:421px;height:300px;border:7px solid #eee;background:linear-gradient(90deg,#9fb0c4 0%,#d8d2c8 45%,#e6dcd2 70%,#b9c0c9 100%)}
.program{left:574px;top:1274px;width:540px}
.program h2{font-weight:400;font-size:24px;color:#333;margin-bottom:8px;text-transform:uppercase}
.program .lead{font-family:"Open Sans",sans-serif;font-size:12px;line-height:1.6;color:#444;margin-bottom:12px}
.program ul{list-style:none}
.program li{display:flex;align-items:center;gap:12px;font-family:"Open Sans",sans-serif;font-size:13px;color:#555;height:30px}
.program .btn{margin-top:16px;padding:10px 27px;font-size:15px;font-weight:500}
.reviews{left:0;top:1672px;width:1200px;height:293px;background:var(--blue)}
.reviews-pill{left:457px;top:1646px;width:284px;height:54px;border-radius:27px;background:var(--red);border:3px solid var(--white);color:var(--white);font-size:23px;display:flex;align-items:center;justify-content:center;z-index:2}
.review{top:1774px;display:flex;gap:22px;width:480px}
.review .avatar{flex:none;width:124px;height:124px;border-radius:50%;border:4px solid var(--white)}
.review blockquote{color:var(--white);font-style:italic;font-size:12px;line-height:1.75;padding-top:10px}
.review blockquote b{font-size:22px;font-style:normal;line-height:0;vertical-align:-6px;margin-right:3px}
.stars{color:#f2b71f;font-size:12px;letter-spacing:1px;margin-top:4px}
.stars span{color:#d8d8d8}
.review cite{display:block;font-style:normal;color:var(--white);font-size:13px;margin-top:6px;text-transform:uppercase}
.footer{left:0;top:1965px;width:1200px;height:227px;background:var(--light)}
.footer-brand{left:99px;top:2030px;display:flex;align-items:center;gap:8px;font-weight:700;font-size:19px;color:var(--blue)}
.footer-brand i{width:18px;height:18px;border-radius:50%;background:var(--red);display:block}
.footer-social{left:122px;top:2095px;display:flex;gap:8px}
.footer-social span{width:22px;height:22px;background:var(--blue);display:block}
.footer-social span:first-child{background:var(--red)}
.fcol h4{font-family:"Open Sans",sans-serif;font-weight:400;font-size:15px;color:#333;margin-bottom:12px;text-transform:uppercase}
.links a{display:block;font-family:"Open Sans",sans-serif;font-size:11px;color:#444;text-decoration:none;line-height:23px;text-transform:uppercase}
.newsletter p{font-family:"Open Sans",sans-serif;font-size:11.5px;line-height:1.7;color:#444;width:262px;text-align:justify;margin-bottom:12px}
.subscribe{display:flex;width:263px;height:44px;border-radius:22px;overflow:hidden;border:1px solid #ddd;background:var(--white)}
.subscribe span{flex:1;font-size:11px;color:#444;display:flex;align-items:center;padding-left:14px}
.subscribe b{width:94px;background:var(--red);color:var(--white);font-weight:400;font-size:11px;display:flex;align-items:center;justify-content:center;text-transform:uppercase}
.fcontact p{font-family:"Open Sans",sans-serif;font-size:13px;color:#333;line-height:1.5}
.fcontact .row{display:flex;align-items:center;gap:12px;font-family:"Open Sans",sans-serif;font-size:14px;color:#333;margin-top:10px}
.bottom-bar{left:0;top:2192px;width:1200px;height:50px;background:var(--footer-bar);color:#ddd;font-size:11px;display:flex;align-items:center;justify-content:center}
</style>
</head>
<body>
<div class="abs top-rule"></div>

<div class="abs social" aria-label="Social links"><span></span><span></span><span></span><span></span></div>
<div class="abs brand"><i></i>Brightleaf Rx Pass</div>
<div class="abs contact-top">
  <div class="ico"><svg width="16" height="16" viewBox="0 0 24 24"><path fill="#fff" d="M6.6 10.8a15 15 0 0 0 6.6 6.6l2.2-2.2c.3-.3.7-.4 1-.2 1.1.4 2.3.6 3.6.6.6 0 1 .4 1 1V20c0 .6-.4 1-1 1A17 17 0 0 1 3 4c0-.6.4-1 1-1h3.5c.6 0 1 .4 1 1 0 1.3.2 2.5.6 3.6.1.3 0 .7-.2 1z"/></svg></div>
  <div>Call us &nbsp;(+555)-210-7734<br><span style="font-size:13px">info@brightleafrxpass.com</span></div>
</div>

<div class="abs hero" role="img" aria-label="Photo of a pharmacist in a white coat holding out an orange prescription bottle"></div>
<nav class="abs nav">
  <a class="active">Home</a><a>About Brightleaf Rx</a><a style="padding:0 38px">Get Card</a><a style="padding:0 38px">Pharmacies</a><a style="padding:0 32px">Drug Pricing</a><a style="padding:0 32px">FAQ</a><a style="border:none">Contact Us</a>
</nav>
<svg class="abs hero-arrow" style="left:46px" width="32" height="64" viewBox="0 0 32 64"><path d="M28 4 4 32l24 28" fill="none" stroke="rgba(255,255,255,.7)" stroke-width="2"/></svg>
<svg class="abs hero-arrow" style="left:1140px" width="32" height="64" viewBox="0 0 32 64"><path d="M4 4l24 28L4 60" fill="none" stroke="rgba(255,255,255,.7)" stroke-width="2"/></svg>
<div class="abs hero-copy">
  <h1>WE HELP INDIVIDUALS</h1>
  <p>that have little or no prescription coverage and allow them to receive a discount ranging from 33% up to 78% for free.</p>
  <span class="btn">Get Free Card</span>
</div>

<svg class="abs mission" viewBox="0 0 1200 192" preserveAspectRatio="none">
  <rect width="1200" height="192" fill="#1d5ba6"/>
  <path d="M345 192 Q318 70 306 28 Q300 2 334 0 H1200 V192 Z" fill="#ec3833"/>
</svg>
<div class="abs mission-title">OUR<br>MISSION</div>
<div class="abs mission-text">
  <p>The Brightleaf Rx Pass is a FREE prescription assistance program that is available to everyone regardless of residency, age or income. This program is designed to assist those with no prescription coverage or for those whose prescription is not covered by insurance.</p>
  <p>This card will provide you with Rx medication savings of up to 75% at more than 60,000 pharmacies across the country including CareStop/pharmacy, Wellgate, Right Path, Tallymart, ValuHaus, Safehaven, Grandway, Kestrel Mart, Morrow's, Hollis Tanner, Prime Fresh and many more.</p>
</div>

<div class="abs howto"></div>
<div class="abs howto-head">
  <h2>HOW TO <em>USE YOUR</em> CARD</h2>
  <a>View Frequently Asked Questions</a>
</div>
<div class="abs step" style="left:110px">
  <div class="circle"><svg width="40" height="36" viewBox="0 0 40 36"><rect x="10" y="1" width="20" height="10" fill="#fff"/><rect x="1" y="12" width="38" height="16" rx="3" fill="#fff"/><rect x="9" y="22" width="22" height="13" fill="#fff" stroke="#1d5ba6" stroke-width="2"/></svg></div>
  <h3>Print Card</h3>
  <p>Lorem ipsum dolor sit amet, consectetur adipiscing elit, sed do eiusmod tempor incididunt ut labore et dolore magna aliqua. Ut enim ad minim</p>
</div>
<div class="abs step" style="left:445px">
  <div class="circle"><svg width="40" height="36" viewBox="0 0 40 36"><path d="M14 8V3h12v5" fill="none" stroke="#fff" stroke-width="3"/><rect x="1" y="8" width="38" height="27" rx="3" fill="#fff"/><path d="M20 14v15M12.5 21.5h15" stroke="#1d5ba6" stroke-width="4"/></svg></div>
  <h3>Present Card At Pharmacy</h3>
  <p>Lorem ipsum dolor sit amet, consectetur adipiscing elit, sed do eiusmod tempor incididunt ut labore et dolore magna aliqua. Ut enim ad minim</p>
</div>
<div class="abs step" style="left:787px">
  <div class="circle">$</div>
  <h3>Save Money</h3>
  <p>Lorem ipsum dolor sit amet, consectetur adipiscing elit, sed do eiusmod tempor incididunt ut labore et dolore magna aliqua. Ut enim ad minim</p>
</div>

<div class="abs program-photo" role="img" aria-label="Photo of a pharmacist handing medication to a senior customer at a pharmacy counter"></div>
<div class="abs program">
  <h2>Free Prescription Assistance Program</h2>
  <p class="lead">Lorem ipsum dolor sit amet, consectetur adipiscing elit, sed do eiusmod tempor incididunt ut labore et dolore magna aliqua. Ut enim ad minim veniam.</p>
  <ul>
    <li><svg width="14" height="12" viewBox="0 0 14 12"><path d="M1 6l4 4 8-9" fill="none" stroke="#1d5ba6" stroke-width="2.5"/></svg>Completely FREE Prescription Assistance Program</li>
    <li><svg width="14" height="12" viewBox="0 0 14 12"><path d="M1 6l4 4 8-9" fill="none" stroke="#1d5ba6" stroke-width="2.5"/></svg>LOWEST PRICE logic to guarantee that you get the best deal on your prescriptions</li>
    <li><svg width="14" height="12" viewBox="0 0 14 12"><path d="M1 6l4 4 8-9" fill="none" stroke="#1d5ba6" stroke-width="2.5"/></svg>Instant printable membership card ready to use</li>
    <li><svg width="14" height="12" viewBox="0 0 14 12"><path d="M1 6l4 4 8-9" fill="none" stroke="#1d5ba6" stroke-width="2.5"/></svg>Savings of up to 75% at more than 60,000 national and regional pharmacies</li>
    <li><svg width="14" height="12" viewBox="0 0 14 12"><path d="M1 6l4 4 8-9" fill="none" stroke="#1d5ba6" stroke-width="2.5"/></svg>This card is pre-activated and can be used Immediately</li>
  </ul>
  <span class="btn">Get Free Card</span>
</div>

<div class="abs reviews"></div>
<div class="abs reviews-pill">Customer Reviews</div>
<div class="abs review" style="left:96px">
  <div class="avatar" role="img" aria-label="Customer portrait photo" style="background:linear-gradient(135deg,#c9b7a6,#7b5a45)"></div>
  <div>
    <blockquote><b>&ldquo;</b>Lorem ipsum dolor sit amet, consectetur adipiscing elit, sed do eiusmod tempor incididunt ut labore et dolore magna aliqua. Ut enim ad minim veniam, quis nostrud</blockquote>
    <div class="stars">&#9733;&#9733;&#9733;<span>&#9733;&#9733;</span></div>
    <cite>John Doe</cite>
  </div>
</div>
<div class="abs review" style="left:641px">
  <div class="avatar" role="img" aria-label="Customer portrait photo" style="background:linear-gradient(135deg,#e8e8ea,#9a8578)"></div>
  <div>
    <blockquote><b>&ldquo;</b>Lorem ipsum dolor sit amet, consectetur adipiscing elit, sed do eiusmod tempor incididunt ut labore et dolore magna aliqua. Ut enim ad minim veniam, quis nostrud</blockquote>
    <div class="stars">&#9733;&#9733;&#9733;<span>&#9733;&#9733;</span></div>
    <cite>John Doe</cite>
  </div>
</div>

<footer>
  <div class="abs footer"></div>
  <div class="abs footer-brand"><i></i>Brightleaf Rx Pass</div>
  <div class="abs footer-social" aria-label="Social links"><span></span><span></span><span></span><span></span></div>
  <div class="abs fcol links" style="left:335px;top:2007px">
    <h4>Information</h4>
    <a>Get Card</a><a>FAQ</a><a>Pharmacies</a><a>Drug Pricing</a><a>Contact</a>
  </div>
  <div class="abs fcol newsletter" style="left:565px;top:2007px">
    <h4>Sign Up For Newsletter</h4>
    <p>Excepteur sint occaecat cupidatat non proide sunt in culpa qui officia deserunt</p>
    <div class="subscribe"><span>Enter Name</span><b>Subscribe</b></div>
  </div>
  <div class="abs fcol fcontact" style="left:912px;top:2007px">
    <h4>Contact Us</h4>
    <p>The Brightleaf Rx Pass<br>PO BOX TBA, Maplecrest</p>
    <div class="row"><svg width="18" height="18" viewBox="0 0 24 24"><path fill="none" stroke="#ec3833" stroke-width="1.8" d="M6.6 10.8a15 15 0 0 0 6.6 6.6l2.2-2.2c.3-.3.7-.4 1-.2 1.1.4 2.3.6 3.6.6.6 0 1 .4 1 1V20c0 .6-.4 1-1 1A17 17 0 0 1 3 4c0-.6.4-1 1-1h3.5c.6 0 1 .4 1 1 0 1.3.2 2.5.6 3.6.1.3 0 .7-.2 1z"/></svg>+1 05 4410 2286</div>
    <div class="row" style="font-size:13px;margin-top:6px"><svg width="18" height="14" viewBox="0 0 18 14"><rect x="1" y="1" width="16" height="12" fill="none" stroke="#ec3833" stroke-width="1.5"/><path d="M1 1l8 7 8-7" fill="none" stroke="#ec3833" stroke-width="1.5"/></svg>info@brightleafrxpass.com</div>
  </div>
  <div class="abs bottom-bar">&copy;2015 - 2016 The Brightleaf Rx Pass., All Rights Reserved.</div>
</footer>
</body>
</html>
```